RW Framewell Inc Business cards

We need business cards using our existing logo but slightly modified. Right now the logo says RW Loadbearing Masonry. We want to keep the RW part of the design, but replace the Structural Concrete portion with "FRAMEWELL". Please see the attached file.
Ideally this would be a blank template so we can add Different Names, titles, and phone numbers later.
On the one side we want only the logo and on the other side the detail. I'm attaching an example for you to see.
Please reach out with any other questions. Our address and other details will be given out once we find a design we like.

Target Market(s)

Construction Industry

```html
<!DOCTYPE html>
<html lang="en">
<head>
<meta charset="utf-8">
<title>RW Framewell Inc – Business Card</title>
<link href="https://fonts.googleapis.com/css2?family=Roboto:wght@400;500&family=Open+Sans:wght@600&display=swap" rel="stylesheet">
<style>
  :root {
    --page-bg: #d9d4cd;
    --card-clear: #eceef0;
    --card-blue: #2f5e9c;
    --curve-edge: #8b8680;
    --brand-grey: #55534f;
    --name-tan: #e4cfaa;
    --detail-light: #dfe7f1;
    --address-tan: #d6c3a1;
  }
  * { margin: 0; padding: 0; box-sizing: border-box; }
  html, body {
    width: 1200px; height: 1054px; overflow: hidden;
    background: var(--page-bg);
  }
  .business-card {
    position: absolute; left: 100px; top: 232px;
    width: 1000px; height: 590px;
    background: var(--card-clear);
    box-shadow: 0 10px 30px rgba(0,0,0,0.18);
    overflow: hidden;
  }
  .card-shapes { position: absolute; inset: 0; }
  .brand {
    position: absolute; left: 76px; top: 190px;
    color: var(--brand-grey);
    font-family: "Roboto", sans-serif; font-weight: 500;
  }
  .brand-initials { display: block; font-size: 176px; line-height: 160px; letter-spacing: 4px; }
  .brand-name { display: block; font-size: 38px; letter-spacing: 8px; margin-top: 14px; }
  .details {
    position: absolute; left: 601px; top: 140px;
    font-family: "Roboto", sans-serif;
  }
  .person-name {
    font-family: "Open Sans", sans-serif; font-weight: 600;
    font-size: 36px; color: var(--name-tan); line-height: 44px;
  }
  .person-title { font-size: 24px; color: var(--name-tan); margin-top: 2px; }
  .contact-list { list-style: none; margin-top: 46px; }
  .contact-list li {
    display: flex; align-items: center; gap: 20px;
    font-size: 24px; color: var(--detail-light); height: 38px;
  }
  .contact-list svg { width: 20px; height: 20px; fill: var(--detail-light); flex: none; }
  .address { margin-top: 14px; font-size: 24px; line-height: 38px; color: var(--address-tan); }
</style>
</head>
<body>
  <div class="business-card">
    <svg class="card-shapes" viewBox="0 0 1000 590" width="1000" height="590" aria-hidden="true">
      <path class="curve-edge" d="M428 0 Q618 295 424 590 L440 590 Q640 295 433 0 Z" fill="var(--curve-edge)"/>
      <path class="blue-panel" d="M433 0 Q640 295 440 590 L1000 590 L1000 0 Z" fill="var(--card-blue)"/>
    </svg>

    <div class="brand">
      <span class="brand-initials">RW</span>
      <span class="brand-name">FRAMEWELL</span>
    </div>

    <div class="details">
      <p class="person-name">Daniel RW Hart</p>
      <p class="person-title">Managing Director</p>
      <ul class="contact-list">
        <li>
          <svg viewBox="0 0 20 20"><path d="M2 6c0-2 3-3 8-3s8 1 8 3v2h-4V6H6v2H2z M5 9h10l2 8H3z M10 11a2.5 2.5 0 1 0 0 5a2.5 2.5 0 1 0 0-5z"/></svg>
          555-014-2290
        </li>
        <li>
          <svg viewBox="0 0 20 20"><path d="M2 4h16v12H2z M3.5 5.5 10 11l6.5-5.5v-0z" fill-rule="evenodd"/></svg>
          daniel@framewell-example.com
        </li>
        <li>
          <svg viewBox="0 0 20 20"><path d="M10 2a8 8 0 1 0 0 16a8 8 0 1 0 0-16z M4 9h3c0-2 .6-4 1.5-5A6 6 0 0 0 4 9z M9 9h2c0-2-.4-3.6-1-4.6C9.4 5.4 9 7 9 9z M13 9h3a6 6 0 0 0-4.5-5C12.4 5 13 7 13 9z M4 11a6 6 0 0 0 4.5 5c-.9-1-1.5-3-1.5-5z M9 11c0 2 .4 3.6 1 4.6.6-1 1-2.6 1-4.6z M13 11c0 2-.6 4-1.5 5a6 6 0 0 0 4.5-5z"/></svg>
          www.framewell-example.com
        </li>
      </ul>
      <p class="address">18 Timberline Rd., Oakridge,<br>Oregon, US 97463</p>
    </div>
  </div>
</body>
</html>
```